automotive repair and collision repair shop card

our company is called K.L Motor service we are a automotive repair company
we also do government inspections. the company information is on the cards. I would like you to use my new logo and create a new card and use the information from my old card. Good Luck!!

Industry/Entity Type

Car Repair

Contact Information for Business Card

Address: #417-18842 52 Ave, Surrey, BC V5K 8R3
Phone:(604) 555-0187
fax 604 555 0193
website www.klmotorworks.example

Font styles to use
Serif
Sans Serif

Requirements
Must have
• all the information
Should not have
• the owner and there name

```html
<!DOCTYPE html>
<html lang="en">
<head>
<meta charset="utf-8">
<title>K.L Motor Service – Business Card</title>
<link rel="stylesheet" href="https://fonts.googleapis.com/css2?family=Saira+Condensed:wght@400;600;700&display=swap">
<style>
  :root {
    --bg: #e9e6e1;
    --card-white: #f7f7f7;
    --card-shade: #e2e2e2;
    --ink: #1b1b1b;
    --ink-soft: #555555;
    --card-black: #0d0d0d;
    --card-black-2: #262626;
    --on-dark: #f2f2f2;
    --on-dark-soft: #bdbdbd;
    --photo-dark: #2a2a2c;
    --photo-light: #9a9a9c;
  }
  * { box-sizing: border-box; margin: 0; padding: 0; }
  html, body { width: 1200px; height: 892px; overflow: hidden; }
  body {
    background: var(--bg);
    font-family: "Saira Condensed", "Arial Narrow", sans-serif;
    color: var(--ink);
    position: relative;
  }

  /* Front card */
  .card-front {
    position: absolute;
    left: 80px; top: 126px;
    width: 380px; height: 640px;
    background: radial-gradient(ellipse at 55% 35%, var(--card-white) 0%, var(--card-white) 55%, var(--card-shade) 100%);
    box-shadow: 0 10px 28px rgba(0,0,0,0.18);
  }
  .brand {
    position: absolute; top: 150px; left: 20px; right: 20px;
    text-align: center;
  }
  .brand-name {
    display: inline-flex; align-items: center; gap: 10px;
    font-size: 38px; font-weight: 600; letter-spacing: 1px;
    color: var(--ink); line-height: 1; white-space: nowrap;
  }
  .brand-dot {
    width: 14px; height: 14px; border-radius: 50%;
    background: var(--ink); flex: none;
  }
  .brand-tagline {
    margin-top: 8px;
    font-size: 18px; font-weight: 400; letter-spacing: 1px;
    color: var(--ink-soft);
  }
  .contact {
    position: absolute; top: 430px; left: 20px; right: 20px;
    list-style: none; text-align: center;
    font-size: 18px; line-height: 1.6; color: var(--ink);
  }

  /* Back card */
  .card-back {
    position: absolute;
    left: 520px; top: 246px;
    width: 620px; height: 380px;
    background: linear-gradient(135deg, var(--card-black-2) 0%, var(--card-black) 60%);
    box-shadow: 0 10px 28px rgba(0,0,0,0.25);
    overflow: hidden;
  }
  .back-edge {
    position: absolute; left: 0; top: 0; bottom: 0; width: 26px;
    background: var(--card-white);
  }
  .back-photo {
    position: absolute; left: 26px; top: 0; bottom: 0; width: 270px;
    background: radial-gradient(ellipse at 45% 60%, var(--photo-light) 0%, var(--photo-dark) 55%, var(--card-black) 100%);
  }
  .services {
    position: absolute; left: 330px; top: 40px;
    color: var(--on-dark);
  }
  .services-title { font-size: 20px; font-weight: 600; margin-bottom: 8px; }
  .services-list { list-style: none; font-size: 22px; font-weight: 600; line-height: 1.35; }
  .back-brand {
    position: absolute; right: 30px; bottom: 34px; text-align: right;
    color: var(--on-dark);
  }
  .back-brand-name { font-size: 32px; font-weight: 600; letter-spacing: 1px; line-height: 1; }
  .back-brand-tagline { font-size: 13px; color: var(--on-dark-soft); margin-top: 4px; }
</style>
</head>
<body>

  <section class="card-front" aria-label="Business card front">
    <div class="brand">
      <div class="brand-name"><span class="brand-dot"></span>K.L MOTOR SERVICE</div>
      <div class="brand-tagline">One Stop Repair Shop</div>
    </div>
    <ul class="contact">
      <li>E : info@klmotorworks.example</li>
      <li>W : www.klmotorworks.example</li>
      <li>P : (604) 555-0187 / F : 604 555 0193</li>
      <li>A : #417-18842 52 Ave, Surrey, BC V5K 8R3</li>
    </ul>
  </section>

  <section class="card-back" aria-label="Business card back">
    <div class="back-edge"></div>
    <div class="back-photo" role="img" aria-label="Photo of a dark grey sports car with red brake calipers"></div>
    <div class="services">
      <div class="services-title">Contact us for :</div>
      <ul class="services-list">
        <li>Brake Service</li>
        <li>General Maintenance</li>
        <li>Glass Replacement</li>
        <li>Insurer Claims</li>
        <li>Inspections</li>
        <li>Engine repair</li>
      </ul>
    </div>
    <div class="back-brand">
      <div class="back-brand-name">K.L MOTOR SERVICE</div>
      <div class="back-brand-tagline">One Stop Repair Shop</div>
    </div>
  </section>

</body>
</html>
```